Website for Plumbing Company, Mr. FlowKettle

I need a 7-page fully HTML-coded website for my plumbing company, Mr. FlowKettle. We specialize in installation, repair, and replacement of both gas and electric water heaters. Although we offer both tankless (on-demand) water heaters and standard (with tank) water heaters, most of our business is related to standard (with tank) water heaters in the USA market.

These are the pages I need:
1. Home page with sections such as About Us, Our Services, Why Choose Us, Testimonials, Location Map (Palm Beach County Florida), Quote Request Form, Join Our Newsletter, Mission Statement, etc.

2. Gas Water Heaters

3. Electric Water Heaters

4. Tankless Water Heaters

5. About Us

6. Contact Us

7. Privacy Policy, Terms & Conditions

Be sure to mention the following points:
1. Same-Day Service
2. Best Price Guarantee
3. 100% Satisfaction Rating
4. 15-Year Warranty on Water Heater & Parts
5. Lifetime Warranty on Workmanship
*All Warranties are Transferrable Upon Home Sale

Once design is selected and finalized, I need the website coded in a standard HTML/CSS and temporarily hosted on your development server so I can see the website functionality that is not observable from screenshots, such as section animations, etc. Once those details are finalized, I will move the source code to my server and complete the project.

Residential Home Owners and Business Owners

Plumbing, Home Services, Remodeling, Construction

0054AA
0677BA
7BADD7
CADEEF
E8F1F8
FFC000
F8CF3A
FAE287
FDF2CF
FEFAEE
EE7325
F08F49
F5BC92
FAE3D3
FDF4ED

• Clean, colorful, and professional

```html
<!DOCTYPE html>
<html lang="en">
<head>
<meta charset="utf-8">
<title>Contact Us – Mr. FlowKettle</title>
<link rel="stylesheet" href="https://fonts.googleapis.com/css2?family=Manrope:wght@400;500;600;700;800&display=swap">
<style>
:root{
  --navy:#0c1f5c;
  --navy-dark:#0a1124;
  --blue:#0677ba;
  --nav-blue:#1a84e6;
  --yellow:#ffc000;
  --yellow-soft:#ffcc00;
  --ink:#0c1f5c;
  --grey-text:#6b7391;
  --panel:#f2f2f2;
  --line:#e4e6ec;
  --white:#fff;
}
*{box-sizing:border-box;margin:0;padding:0}
html,body{width:1200px;height:2208px;overflow:hidden}
body{font-family:"Manrope",sans-serif;color:var(--ink);background:var(--white);position:relative}
.abs{position:absolute}
svg{display:block}

/* top bar */
.topbar{left:0;top:0;width:1200px;height:36px;background:var(--navy-dark);color:#fff;font-size:12px}
.topbar .serving{left:60px;top:10px;display:flex;align-items:center;gap:6px}
.topbar .dot{width:16px;height:16px;border-radius:50%;background:var(--yellow)}
.topbar .links{right:60px;top:10px;display:flex;gap:28px}

/* header */
.logo{left:60px;top:48px;display:flex;align-items:center;gap:6px;font-weight:800;font-size:18px;color:var(--blue)}
.logo .mark{width:18px;height:18px;border-radius:50%;background:var(--yellow)}
.search{left:247px;top:61px;width:233px;height:37px;border:1px solid #ddd}
.search svg{position:absolute;right:10px;top:10px}
.contact-chip{display:flex;align-items:center;gap:12px;top:57px}
.contact-chip .ico{width:41px;height:41px;border-radius:50%;background:var(--yellow);display:flex;align-items:center;justify-content:center}
.contact-chip small{display:block;font-size:11.5px;color:var(--grey-text)}
.contact-chip b{display:block;font-size:15px;font-weight:700;color:var(--navy);margin-top:2px}

/* nav */
.nav{left:60px;top:122px;width:903px;height:67px;background:var(--nav-blue);display:flex;align-items:center;padding-left:30px;color:#fff;font-size:15.5px;font-weight:600}
.nav span{display:flex;align-items:center}
.nav .sep{width:5px;height:5px;border-radius:50%;background:var(--yellow);margin:0 20px}
.nav .current{color:var(--yellow)}
.callback{left:963px;top:122px;width:180px;height:67px;background:var(--yellow-soft);font-size:13.5px;font-weight:700;display:flex;align-items:center;justify-content:center;color:#111}

/* hero */
.hero{left:0;top:154px;width:1200px;height:334px;background:linear-gradient(90deg,#3a3f48 0%,#5b6170 40%,#3e5684 75%,#1f4fa0 100%);z-index:-1}
.hero-title{left:0;width:1200px;top:258px;text-align:center;color:#fff;font-size:40px;font-weight:800}
.hero-bar{left:544px;top:322px;width:112px;height:5px;background:var(--yellow)}
.crumbs{left:0;width:1200px;top:360px;display:flex;justify-content:center;gap:14px;font-size:18px;color:#fff;align-items:center}
.crumbs .here{color:var(--yellow)}

/* head offices */
.eyebrow{left:76px;top:583px;display:flex;align-items:center;gap:6px;color:var(--yellow);font-size:13px;font-weight:700}
.h-offices{left:76px;top:604px;font-size:37px;font-weight:800}
.intro{left:596px;top:584px;width:540px;border-left:1.5px solid #999;padding-left:16px;font-size:13.5px;line-height:1.35;color:var(--grey-text);height:65px}
.info{top:706px;display:flex;align-items:center;gap:10px}
.info .ico{width:53px;height:53px;border-radius:50%;display:flex;align-items:center;justify-content:center}
.info b{display:block;font-size:18px;font-weight:700}
.info span{display:block;font-size:14px;margin-top:4px}
.rule{left:74px;top:812px;width:1051px;height:1px;background:var(--line)}

/* form */
.form{left:76px;top:866px;width:583px;height:418px;background:var(--panel)}
.field{left:21px;width:527px;background:#fff;font-size:12.5px;color:#555;padding:15px 18px;font-weight:500}
.submit{left:21px;top:353px;width:132px;height:40px;background:var(--yellow-soft);font-size:11px;font-weight:700;display:flex;align-items:center;justify-content:center;letter-spacing:.3px}

/* branch */
.h-branch{left:708px;top:864px;font-size:37px;font-weight:800}
.branch-intro{left:713px;top:920px;width:360px;font-size:13.5px;color:var(--grey-text);line-height:1.3}
.bcard{left:715px;width:410px;height:75px;display:flex;align-items:center;gap:14px;padding-left:32px}
.bcard b{display:block;font-size:14.5px;font-weight:700}
.bcard span{display:block;font-size:12.5px;margin-top:5px}
.bcard.yellow{background:var(--yellow-soft);color:#111}
.bcard.navy{background:var(--navy);color:#fff}

/* map */
.map{left:0;top:1444px;width:1200px;height:372px;background:linear-gradient(120deg,#dfe9e2 0%,#e8ecef 45%,#d9e3ee 75%,#c9daf0 100%)}
.map-card{top:37px;width:287px;height:100px;display:flex}
.map-card .photo{width:84px;height:100px;background:linear-gradient(180deg,#e9e9e6,#a08a6e)}
.map-card .txt{flex:1;padding:22px 0 0 27px}
.map-card b{display:block;font-size:21px;font-weight:700}
.map-card span{display:block;font-size:12.5px;margin-top:8px}
.map-card.navy .txt{background:var(--navy);color:#fff}
.map-card.yellow .txt{background:var(--yellow-soft);color:var(--navy)}
.sat{left:79px;top:250px;width:90px;height:92px;border:3px solid #fff;border-radius:6px;background:linear-gradient(135deg,#3e4a38,#6e7a5a);color:#fff;font-size:12px;font-weight:700;display:flex;align-items:flex-end;justify-content:center;padding-bottom:10px}
.zoom{left:1088px;top:243px;width:36px;height:112px}
.zoom div{background:#fff;border-radius:18px;box-shadow:0 1px 4px rgba(0,0,0,.25);position:absolute;left:0;width:36px;display:flex;align-items:center;justify-content:center;font-size:22px;color:#222}

/* footer */
.footer{left:0;top:1816px;width:1200px;height:392px;background:linear-gradient(180deg,#0e1c3f,#0a1230);color:#fff}
.fcol{top:58px}
.fcol h4{font-size:16.5px;font-weight:800;letter-spacing:.2px}
.fcol p{font-size:13px;color:#7c849c;line-height:1.3;margin-top:22px}
.fcol ul{list-style:none;margin-top:26px}
.fcol li{font-size:13.5px;margin-bottom:17px;color:#e6e8ef}
.fcontact{font-size:21px;font-weight:600;line-height:1.3;margin-top:18px}
.socials{display:flex;gap:9px;margin-top:20px}
.socials i{width:38px;height:38px;border-radius:50%;background:#fff;display:block}
.news{left:858px;top:172px;width:280px;height:49px;background:#f0f0f0;color:#333;font-size:13.5px;padding:15px 21px}
.news svg{position:absolute;right:12px;top:14px}
.legal{left:858px;top:238px;width:280px;font-size:13px;line-height:1.3;color:#e6e8ef}
.frule{left:57px;top:324px;width:1081px;height:1px;background:#26304e}
.copy{left:57px;top:350px;font-size:14px;color:#e6e8ef}
.pay{top:342px;height:28px;width:52px;border-radius:3px}
</style>
</head>
<body>

<div class="abs topbar">
  <div class="abs serving"><i class="dot"></i>Serving Palm Beach County &amp; Surroundings</div>
  <div class="abs links"><span>Get Help</span><span>FAQ</span><span>My Account</span></div>
</div>

<div class="abs logo"><i class="mark"></i>Mr. FlowKettle</div>
<div class="abs search"><svg width="16" height="16" viewBox="0 0 16 16"><circle cx="7" cy="7" r="5.5" fill="none" stroke="#aaa" stroke-width="1.4"/><path d="M11 11l4 4" stroke="#aaa" stroke-width="1.4"/></svg></div>

<div class="abs contact-chip" style="left:515px">
  <div class="ico"><svg width="18" height="14" viewBox="0 0 18 14"><rect x="1" y="1" width="16" height="12" fill="none" stroke="#0c1f5c" stroke-width="1.6"/><path d="M1 1l8 7 8-7" fill="none" stroke="#0c1f5c" stroke-width="1.6"/></svg></div>
  <div><small>Email Us</small><b>hello@flowkettle.com</b></div>
</div>
<div class="abs contact-chip" style="left:750px">
  <div class="ico"><svg width="18" height="18" viewBox="0 0 24 24"><path d="M5 3h4l2 5-3 2a12 12 0 006 6l2-3 5 2v4a2 2 0 01-2 2A18 18 0 013 5a2 2 0 012-2z" fill="none" stroke="#0c1f5c" stroke-width="1.8"/></svg></div>
  <div><small>Call us any time</small><b>+1 (561) 555-0142</b></div>
</div>
<div class="abs contact-chip" style="left:963px">
  <div class="ico"><svg width="16" height="20" viewBox="0 0 16 20"><path d="M8 19s-6-7-6-11a6 6 0 0112 0c0 4-6 11-6 11z" fill="none" stroke="#0c1f5c" stroke-width="1.6"/><circle cx="8" cy="8" r="2.2" fill="none" stroke="#0c1f5c" stroke-width="1.6"/></svg></div>
  <div><small>Locations</small><b>412 Harbor Lane, US</b></div>
</div>

<div class="abs hero" role="img" aria-label="Photo of an electrician in safety glasses working on a breaker panel"></div>

<nav class="abs nav">
  <span>Home</span><i class="sep"></i><span>About Us</span><i class="sep"></i><span>Gas Water Heaters</span><i class="sep"></i><span>Electric Water Heaters</span><i class="sep"></i><span>Tankless</span><i class="sep"></i><span class="current">Contact us</span>
</nav>
<div class="abs callback">Request a Call Back</div>

<h1 class="abs hero-title">Contact Us</h1>
<div class="abs hero-bar"></div>
<div class="abs crumbs"><span>Home</span>
  <svg width="20" height="18" viewBox="0 0 20 18"><path d="M2 2l7 7-7 7M10 2l7 7-7 7" fill="none" stroke="#ffc000" stroke-width="2.4"/></svg>
  <span class="here">Contact Us</span></div>

<div class="abs eyebrow"><svg width="10" height="14" viewBox="0 0 10 14"><path d="M6 0L0 8h4l-1 6 7-9H6z" fill="#ffc000"/></svg>CONTAC US</div>
<h2 class="abs h-offices">Our head offices</h2>
<p class="abs intro">Find a location nearest you to reduce shipping costs and make shopping easier. Sign up for 10% off your first purchase and free shipping. Updates information on Sales and Offers.</p>

<div class="abs info" style="left:76px">
  <div class="ico" style="background:var(--navy)"><svg width="20" height="24" viewBox="0 0 16 20"><path d="M8 19s-6-7-6-11a6 6 0 0112 0c0 4-6 11-6 11z" fill="none" stroke="#fff" stroke-width="1.5"/><circle cx="8" cy="8" r="2.2" fill="none" stroke="#fff" stroke-width="1.5"/></svg></div>
  <div><b>Our Location</b><span>412 Harbor Lane, US</span></div>
</div>
<div class="abs info" style="left:347px">
  <div class="ico" style="background:var(--yellow);width:61px;height:61px"><svg width="26" height="26" viewBox="0 0 24 24"><path d="M5 3h4l2 5-3 2a12 12 0 006 6l2-3 5 2v4a2 2 0 01-2 2A18 18 0 013 5a2 2 0 012-2z" fill="none" stroke="#0c1f5c" stroke-width="1.4"/></svg></div>
  <div><b>Mobile Number</b><span>+1 (561) 555-0142</span></div>
</div>
<div class="abs info" style="left:619px">
  <div class="ico" style="border:1px solid #ddd"><svg width="24" height="24" viewBox="0 0 24 24"><circle cx="12" cy="12" r="10" fill="none" stroke="#0c1f5c" stroke-width="1.6"/><ellipse cx="12" cy="12" rx="4.5" ry="10" fill="none" stroke="#0c1f5c" stroke-width="1.6"/><path d="M2 12h20" stroke="#0c1f5c" stroke-width="1.6"/></svg></div>
  <div><b>Have Quires ?</b><span>+1 (561) 555-0142</span></div>
</div>
<div class="abs info" style="left:888px">
  <div class="ico" style="background:var(--navy)"><svg width="22" height="18" viewBox="0 0 18 14"><rect x="1" y="1" width="16" height="12" fill="none" stroke="#fff" stroke-width="1.3"/><path d="M1 1l8 7 8-7" fill="none" stroke="#fff" stroke-width="1.3"/></svg></div>
  <div><b>Contact Support</b><span>hello@flowkettle.com</span></div>
</div>
<div class="abs rule"></div>

<form class="abs form">
  <div class="abs field" style="top:38px;height:45px">Your Name</div>
  <div class="abs field" style="top:102px;height:45px">Your Phone Number</div>
  <div class="abs field" style="top:163px;height:45px">Your Email</div>
  <div class="abs field" style="top:228px;height:105px">Message Here</div>
  <div class="abs submit">LET'S TALKS</div>
</form>

<h2 class="abs h-branch">Our Us Branch</h2>
<p class="abs branch-intro">Find a location nearest you to reduce shipping costs and make shopping easier.</p>

<div class="abs bcard yellow" style="top:986px">
  <svg width="24" height="30" viewBox="0 0 24 30"><path d="M9 14V4a2 2 0 014 0v9l6 2a3 3 0 012 3l-1 7H9l-5-7a2 2 0 013-2l2 2" fill="none" stroke="#111" stroke-width="1.5"/></svg>
  <div><b>Chat To Us</b><span>chat@flowkettle.com</span></div>
</div>
<div class="abs bcard navy" style="top:1095px">
  <svg width="22" height="30" viewBox="0 0 16 20"><path d="M8 19s-6-7-6-11a6 6 0 0112 0c0 4-6 11-6 11z" fill="none" stroke="#fff" stroke-width="1.2"/><circle cx="8" cy="8" r="2.2" fill="none" stroke="#fff" stroke-width="1.2"/></svg>
  <div><b>Visit Our Office Branch</b><span>412 Harbor Lane, US</span></div>
</div>
<div class="abs bcard navy" style="top:1205px">
  <svg width="26" height="26" viewBox="0 0 24 24"><path d="M5 3h4l2 5-3 2a12 12 0 006 6l2-3 5 2v4a2 2 0 01-2 2A18 18 0 013 5a2 2 0 012-2z" fill="none" stroke="#fff" stroke-width="1.3"/></svg>
  <div><b>Call Us</b><span>+1 (561) 555-0142</span></div>
</div>

<div class="abs map" role="img" aria-label="Street map of the metro area with office location pin">
  <div class="abs map-card navy" style="left:75px"><div class="photo" role="img" aria-label="Photo of an office interior"></div><div class="txt"><b>US Branch</b><span>Palm Road, 18</span></div></div>
  <div class="abs map-card yellow" style="left:454px"><div class="photo" role="img" aria-label="Photo of an office interior"></div><div class="txt"><b>US Branch</b><span>Lantana Road</span></div></div>
  <div class="abs map-card navy" style="left:840px"><div class="photo" role="img" aria-label="Photo of an office interior"></div><div class="txt"><b>US Branch</b><span>32B Ocean Avenue</span></div></div>
  <svg class="abs" style="left:906px;top:206px" width="34" height="48" viewBox="0 0 34 48"><path d="M17 46S2 26 2 16a15 15 0 0130 0c0 10-15 30-15 30z" fill="#111"/><circle cx="17" cy="16" r="6" fill="#fff"/></svg>
  <div class="abs sat">Satellite</div>
  <div class="abs zoom">
    <div style="top:0;height:36px"><svg width="16" height="16" viewBox="0 0 16 16"><circle cx="8" cy="8" r="4" fill="#222"/><circle cx="8" cy="8" r="6.5" fill="none" stroke="#222"/></svg></div>
    <div style="top:42px;height:70px;flex-direction:column;gap:6px;line-height:1"><span>+</span><span>−</span></div>
  </div>
</div>

<footer class="abs footer">
  <div class="abs fcol" style="left:57px;width:240px">
    <h4 style="font-size:19px">HELP CUSTOMERS</h4>
    <p>Find a location nearest you to reduce shipping costs and make shopping easier.</p>
    <div class="fcontact">+1 (561) 555-0178<br>info@flowkettle.com</div>
    <div class="socials"><i></i><i></i><i></i><i></i></div>
  </div>
  <div class="abs fcol" style="left:361px">
    <h4>OUR COMPANY</h4>
    <ul><li>About us</li><li>Contact us</li><li>Our Store</li><li>FAQ</li><li>Store location</li></ul>
  </div>
  <div class="abs fcol" style="left:584px">
    <h4>SERVICES</h4>
    <ul><li>Gas Water Heaters</li><li>Electric Water Heaters</li><li>Tankless Water Heaters</li></ul>
  </div>
  <div class="abs fcol" style="left:856px;width:280px">
    <h4>SIGN UP TO NEWSLETTER</h4>
    <p>Sign up for 10% off your first purchase and free shipping. Updates information on Sales and Offers.</p>
  </div>
  <div class="abs news">Enter your
    <svg width="20" height="18" viewBox="0 0 20 18"><path d="M1 2l18 0-9 15z" fill="#111"/></svg>
  </div>
  <p class="abs legal">***By entering the e-mail you accept the terms and conditions and the privacy policy.</p>
  <div class="abs frule"></div>
  <div class="abs copy">Copyright © 2025 Mr. FlowKettle - All Rights Reserved.</div>
  <i class="abs pay" style="left:738px;background:#5aa9d6"></i>
  <i class="abs pay" style="left:796px;background:#f7b5c5"></i>
  <i class="abs pay" style="left:854px;background:#1b56b8"></i>
  <i class="abs pay" style="left:912px;background:#1e2540"></i>
  <i class="abs pay" style="left:970px;background:#ffdd00"></i>
  <i class="abs pay" style="left:1028px;background:#1a1f71"></i>
  <i class="abs pay" style="left:1086px;background:#203a8f"></i>
</footer>

</body>
</html>
```